Counseling Practice Business Card

I need a professional looking business card incorporating my new logo that was just completed. Card needs to incorporate my name and title, description of my specialty, my address, my phone number, my fax number, my email and my website URL. I need to be able to choose design on/with different paper colors and textures.
I do not have a lot of business card ideas so I am open to anything but I want bold,sharp, clear card without additional designs other than my logo (see attached file info). I am open to different color backgrounds or paper colors including black. I do not like traditional brackets around area codes in phone number or dashes between numbers in phone number. Am open to other ways of presenting including periods between numbers as appropriate. I do not know enough to know what I like yet but I want card to coordinate and work together with my logo. My practice emphasizes natural mental health interventions so any use of color (with background paper color or the blue and green in my logo) that elicits nature is nice. In addition to black, any natural brown or wood looking background might be desirable also. Most of the offerings so far look very similar and boring.

Target Market(s)

Potential therapy clients and other professionals

Contact Information for Business Card

Card information:
Gerald M. Whitcombe, Ph.D.
Licensed Clinical Psychologist
Integrative Health Coach
4812 Marlowe Ridge Blvd SE
Suite 310
Duluth, GA 30096
(770) 415-2983 phone
(770) 581-4096 fax
drgeraldwhitcombe@quillmarsh.net
brightfernwellness.net

Font styles to use
Serif
Sans Serif
Other font styles liked:
• anything that you think looks crisp, clear and easily readable

Requirements
Must have
• Any color used should coordinate with my logo design (see attached files).
• Card should be printed horizontally so top and bottom are longest sides of rectangle.
• Background color or paper color should complement and highlight logo. Do not like a white background. black, grey, brown or any color my logo would blend well with.
Nice to have
• I would like designer to utilize color to highlight letters/name or phone-fax-web symbols.
• Bottom edge of card could be highlighted if appropriate to an idea.
Should not have
• I would NOT want the card to have a pure white background at all.
• No clear cards.
• Cards should be oriented with long sides on bottom and top, NOT sides. DO NOT LIKE THIS THIN TALL ORIENTATION.

```html
<!DOCTYPE html>
<html lang="en">
<head>
<meta charset="utf-8">
<title>Brightfern Wellness – Business Card</title>
<link href="https://fonts.googleapis.com/css2?family=PT+Sans:wght@400;700&family=PT+Sans+Narrow:wght@700&display=swap" rel="stylesheet">
<style>
  :root{
    --page:#ece8e4;
    --paper:#b98b74;
    --paper-edge:#a47761;
    --ink:#3b2f2b;
    --brand-blue:#2b7fc8;
    --brand-green:#1f8a3e;
  }
  *{box-sizing:border-box;margin:0;padding:0}
  html,body{width:1200px;height:950px;overflow:hidden;background:var(--page)}
  body{position:relative;font-family:"PT Sans",Arial,sans-serif;color:var(--ink)}

  .card{
    position:absolute;left:250px;width:700px;height:400px;
    background:var(--paper);
    border-bottom:3px solid var(--paper-edge);
    box-shadow:0 6px 18px rgba(0,0,0,.18);
  }
  .card--front{top:50px}
  .card--back{top:500px}

  /* front */
  .accent-bar{position:absolute;left:0;top:44px;width:12px;height:70px;background:var(--brand-blue)}
  .identity{position:absolute;left:44px;top:50px}
  .identity__name{
    font-family:"PT Sans Narrow",Arial,sans-serif;font-weight:700;
    font-size:25px;letter-spacing:.5px;text-transform:uppercase;color:var(--brand-blue);line-height:1.1
  }
  .identity__title{font-size:19px;color:var(--brand-green);line-height:1.2;margin-top:3px}

  .brand-mark{position:absolute;right:40px;top:50px;display:flex;align-items:center;gap:12px}
  .brand-mark__dot{width:22px;height:22px;border-radius:50%;background:var(--brand-green)}
  .brand-mark__name{font-weight:700;font-size:34px;line-height:1;color:var(--brand-blue)}

  .divider{position:absolute;left:44px;right:40px;top:198px;height:2px;background:#5a4a44}

  .address{position:absolute;right:40px;top:216px;text-align:right;font-size:17px;line-height:1.45}

  .contact{position:absolute;left:44px;bottom:38px;list-style:none;font-size:16px;line-height:1.55}
  .contact li{display:flex;align-items:center;gap:10px}
  .contact svg{width:14px;height:14px;flex:none}
  .contact .icon-fill{fill:var(--brand-blue)}

  /* back */
  .brand-mark--large{position:absolute;left:0;right:0;top:0;bottom:0;justify-content:center;gap:18px}
  .brand-mark--large .brand-mark__dot{width:40px;height:40px}
  .brand-mark--large .brand-mark__name{font-size:62px}
</style>
</head>
<body>

<section class="card card--front" aria-label="Business card front">
  <div class="accent-bar"></div>
  <div class="identity">
    <p class="identity__name">Gerald M. Whitcombe, Ph.D.</p>
    <p class="identity__title">Licensed Clinical Psychologist</p>
    <p class="identity__title">Integrative Health Coach</p>
  </div>

  <div class="brand-mark">
    <span class="brand-mark__dot"></span>
    <span class="brand-mark__name">Brightfern Wellness</span>
  </div>

  <div class="divider"></div>

  <address class="address" style="font-style:normal">
    4812 Marlowe Ridge Blvd SE<br>
    Suite 310<br>
    Duluth, GA 30096
  </address>

  <ul class="contact">
    <li>
      <svg viewBox="0 0 16 16" aria-hidden="true"><path class="icon-fill" d="M3.5 1l2.5 3-1.5 1.8c.9 2 2.7 3.8 4.7 4.7L11 9l3 2.5-1.2 2.8C7 14 2 9 1.7 2.2z"/></svg>
      (770) 415-2983
    </li>
    <li>
      <svg viewBox="0 0 16 16" aria-hidden="true"><path class="icon-fill" d="M4 1h8v4H4zM1 6h14v6h-3v3H4v-3H1zm4 4v4h6v-4z"/></svg>
      (770) 581-4096
    </li>
    <li>
      <svg viewBox="0 0 16 16" aria-hidden="true"><path class="icon-fill" d="M1 3h14v10H1zm1.5 1.5L8 9l5.5-4.5v-.1h-11z"/></svg>
      drgeraldwhitcombe@quillmarsh.net
    </li>
    <li>
      <svg viewBox="0 0 16 16" aria-hidden="true"><circle class="icon-fill" cx="8" cy="8" r="7"/><path d="M1 8h14M8 1c-3 3.5-3 10.5 0 14M8 1c3 3.5 3 10.5 0 14" stroke="#b98b74" stroke-width="1.2" fill="none"/></svg>
      www.brightfernwellness.net
    </li>
  </ul>
</section>

<section class="card card--back" aria-label="Business card back">
  <div class="brand-mark brand-mark--large">
    <span class="brand-mark__dot"></span>
    <span class="brand-mark__name">Brightfern Wellness</span>
  </div>
</section>

</body>
</html>
```